Print materials for 3-star hotel

We are changing up our print materials (notepads, letterheads, key card jackets, small flyer for the room rates) We are a 3 star business hotel in the Philippines and have mainly used grey tones and clean, simple lines. See attached photos for logo and hotel interior photos.

Target Market(s)

Business

Contact Information for Business Card

Corvale Terrace Hotel
Lindwell Banca Avenue corner Tolenta St Cebu City 6000 Philippines
Tel: +63 32 481 7302
Mobile: +63 917 648 2095
www.corvaleterracehotel.example

Font styles to use
Serif
Sans Serif

Requirements
Must have
• Simple
• Readable font and font size
Nice to have
• Neutral colors, grey and taupes
Should not have
• No purples and bright blues

```html
<!DOCTYPE html>
<html lang="en">
<head>
<meta charset="utf-8">
<title>Corvale Terrace Hotel – Business Card</title>
<link href="https://fonts.googleapis.com/css2?family=Libre+Baskerville:wght@400&display=swap" rel="stylesheet">
<style>
  :root {
    --backdrop: #eceeee;
    --card: #a8a5a7;
    --ink: #eeeced;
    --rule: rgba(238, 236, 237, 0.75);
    --shadow: rgba(60, 58, 60, 0.18);
  }
  * { margin: 0; padding: 0; box-sizing: border-box; }
  html, body {
    width: 1200px;
    height: 900px;
    overflow: hidden;
    background: var(--backdrop);
  }
  .canvas {
    position: relative;
    width: 1200px;
    height: 900px;
    font-family: "Libre Baskerville", "Times New Roman", serif;
    color: var(--ink);
  }
  .card {
    position: absolute;
    left: 290px;
    width: 620px;
    height: 354px;
    background: var(--card);
    box-shadow: 0 6px 18px var(--shadow);
  }
  .card--front { top: 70px; }
  .card--back  { top: 476px; }

  .wordmark {
    display: flex;
    flex-direction: column;
    align-items: center;
    text-align: center;
  }
  .wordmark__square {
    width: 34px;
    height: 34px;
    background: var(--ink);
    margin-bottom: 18px;
  }
  .wordmark__name {
    font-size: 21px;
    letter-spacing: 0.28em;
    text-transform: uppercase;
    white-space: nowrap;
  }
  .wordmark__sub {
    font-size: 11px;
    letter-spacing: 0.6em;
    text-transform: uppercase;
    margin-top: 6px;
    padding-left: 0.6em;
  }
  .card--front .wordmark {
    position: absolute;
    left: 0; right: 0;
    top: 124px;
  }

  .card--back .wordmark {
    position: absolute;
    left: 30px;
    width: 300px;
    top: 140px;
  }
  .card--back .wordmark__name { font-size: 15px; letter-spacing: 0.24em; }
  .card--back .wordmark__sub { font-size: 9px; }
  .card--back .wordmark__square { width: 26px; height: 26px; margin-bottom: 14px; }

  .divider {
    position: absolute;
    left: 350px;
    top: 110px;
    width: 1px;
    height: 150px;
    background: var(--rule);
  }
  .contact {
    position: absolute;
    left: 372px;
    top: 100px;
    font-size: 11.5px;
    line-height: 1.6;
  }
  .contact__name {
    font-size: 17px;
    letter-spacing: 0.04em;
    text-transform: uppercase;
    line-height: 1.2;
  }
  .contact__role { margin-bottom: 12px; }
  .contact__block { margin-bottom: 10px; }
</style>
</head>
<body>
<main class="canvas">
  <section class="card card--front" aria-label="Business card front">
    <div class="wordmark">
      <span class="wordmark__square" aria-hidden="true"></span>
      <span class="wordmark__name">Corvale Terrace</span>
      <span class="wordmark__sub">Hotel</span>
    </div>
  </section>

  <section class="card card--back" aria-label="Business card back">
    <div class="wordmark">
      <span class="wordmark__square" aria-hidden="true"></span>
      <span class="wordmark__name">Corvale Terrace</span>
      <span class="wordmark__sub">Hotel</span>
    </div>
    <div class="divider" aria-hidden="true"></div>
    <div class="contact">
      <p class="contact__name">Adrian Cole</p>
      <p class="contact__role">CEO/Founder</p>
      <div class="contact__block">
        <p>4821 Marlow Ridge Lane</p>
        <p>Talbrook, Oregon 51206</p>
      </div>
      <p>P. 512 806 3471</p>
      <p>c. 740 219 5583</p>
      <p>name@corvaleterracehotel.example</p>
      <p>www.corvaleterracehotel.example</p>
    </div>
  </section>
</main>
</body>
</html>
```